External Window Signage Design – Antiaging Center

I would like to dress our shop windows in order to promote our activities in medical aesthetics, meso-aesthetics, anti-ageing care and classical beauty. In fact, our 350 m² center is located on the first floor of a building where there is a lot of traffic, as well as a bus stop and metro station. And right in front of a twenty-floor building of the Northern Trade Council.
We want to communicate our activities to our customers with photos and text in a storefront window. So that they can what we do and visit our website www.lumavera.be (our site is in French) as well as our social networks, like pictoloop, friendwall,…
We'd like a window signage : Elegant, Modern, New, Pure, Clean
We are located on the corners of a building, where we have 8 windows on one side and 10 windows on the other, the dimensions are :
Windows
• Height: 125 cm
• Width: 130 cm
Small windows
• Height: 134 cm
• Width: 40 cm
I would say let your imagination go free. I will have other projects for the winner.
Don't hesitate to ask me if you need other formats of the logo or color, like white.
Updates

https://www.craftpoolix.com/design/48261937, I'D LIKE TO HAVE A PROJECT LIKE THIS IF POSSIBLE WITH THE LITTLE WINDOW UNDERNEATH AS WELL.

Target Market(s)

People who want to take care of their external appearance, look beautiful and good looking, womens/girls - mens/boys

Requirements
Must have
• Face and silhouette of a woman. Elegant
Serious, Modern, Professional, Feminine,Upmarket
Nice to have
• To put the different treatments that we propose,
Should not have
• We absolutely don't want a classic beauty center signage, which is reviewed many times

```html
<!DOCTYPE html>
<html lang="en">
<head>
<meta charset="utf-8">
<title>Lumavera – Make youth last</title>
<link rel="stylesheet" href="https://fonts.googleapis.com/css2?family=Great+Vibes&family=Montserrat:wght@400;700;800&display=swap">
<style>
  :root {
    --paper: #ffffff;
    --ink: #414042;
    --ink-soft: #5a5a5c;
    --gold: #b09a5e;
    --art-tone: #ecebea;
    --art-fade: #f7f6f5;
  }
  html, body {
    margin: 0;
    padding: 0;
    width: 1200px;
    height: 1154px;
    overflow: hidden;
    background: var(--paper);
  }
  .window-panel {
    position: relative;
    width: 1200px;
    height: 1154px;
    background: var(--paper);
    overflow: hidden;
  }
  .brand {
    position: absolute;
    left: 83px;
    top: 166px;
    display: flex;
    flex-direction: column;
    align-items: center;
  }
  .brand-row {
    display: flex;
    align-items: center;
    gap: 10px;
  }
  .brand-dot {
    width: 14px;
    height: 14px;
    border-radius: 50%;
    background: var(--gold);
  }
  .brand-name {
    font-family: "Montserrat", sans-serif;
    font-weight: 800;
    font-size: 40px;
    letter-spacing: -1.5px;
    color: var(--ink);
    line-height: 1;
  }
  .brand-tagline {
    font-family: "Montserrat", sans-serif;
    font-weight: 400;
    font-size: 13px;
    color: var(--ink-soft);
    margin-top: 4px;
  }
  .headline {
    position: absolute;
    left: 0;
    top: 0;
    margin: 0;
    font-family: "Great Vibes", cursive;
    font-weight: 400;
    color: var(--ink);
    -webkit-text-stroke: 2px var(--ink);
  }
  .headline span {
    position: absolute;
    white-space: nowrap;
    line-height: 1;
  }
  .headline .line-1 { left: 118px; top: 345px; font-size: 205px; }
  .headline .line-2 { left: 95px;  top: 485px; font-size: 235px; }
  .headline .line-3 { left: 170px; top: 660px; font-size: 235px; }
  .website {
    position: absolute;
    left: 83px;
    top: 1036px;
    font-family: "Montserrat", sans-serif;
    font-weight: 700;
    font-size: 35px;
    letter-spacing: 2px;
    color: var(--gold);
    line-height: 1;
  }
  .portrait-art {
    position: absolute;
    left: 660px;
    top: 60px;
    width: 530px;
    height: 1040px;
    background: radial-gradient(ellipse 48% 50% at 55% 48%, var(--art-tone) 0%, var(--art-fade) 55%, var(--paper) 100%);
  }
</style>
</head>
<body>
  <main class="window-panel">
    <header class="brand">
      <div class="brand-row">
        <span class="brand-dot"></span>
        <span class="brand-name">Lumavera</span>
      </div>
      <span class="brand-tagline">Antiaging Center</span>
    </header>

    <h1 class="headline">
      <span class="line-1">Make</span>
      <span class="line-2">youth</span>
      <span class="line-3">last</span>
    </h1>

    <div class="website">www.lumavera.be</div>

    <div class="portrait-art" role="img" aria-label="Single-line drawing of a woman's face with flowing hair, thin black line on white"></div>
  </main>
</body>
</html>
```